Entrepreneur Podcast Cover Graphic Design

My wife and I just launched our podcast but we don't like the current cover. We want a new cover designed so it stands out and reflects the professionalism of our podcast. Attached is our current podcast cover design. We'd like to have it read "Rob & Kolette Talk With Founders About HARD CHOICES" - We'd also like to feature somehow that we have daily tips included.

Target Market(s)

entrepreneurs,business owners,start ups

Industry/Entity Type

Entrepreneur

Font styles to use
Sans Serif

Colors
0355a3
f37122
9bcb3c
fbed22
ec1f27

Requirements
Must have
• Our names listed: Rob & Kolette
Nice to have
• dark, bold colored background with an outline around the edge
Should not have
• no cartoons, no profanity

```html
<!DOCTYPE html>
<html lang="en">
<head>
<meta charset="utf-8">
<title>Rob &amp; Kolette Talk With Founders About Hard Choices</title>
<link rel="stylesheet" href="https://fonts.googleapis.com/css2?family=Roboto:wght@300;700&display=swap">
<style>
  :root {
    --navy: #003264;
    --bubble-light: #e6f5fd;
    --orange: #f37122;
    --red: #ec1f27;
  }
  html, body {
    margin: 0;
    padding: 0;
    width: 1200px;
    height: 1200px;
    overflow: hidden;
    background: var(--navy);
  }
  .cover {
    position: relative;
    width: 1200px;
    height: 1200px;
    background: var(--navy);
    font-family: 'Roboto', Arial, sans-serif;
    overflow: hidden;
  }
  .bubbles {
    position: absolute;
    inset: 0;
  }
  .text-block {
    position: absolute;
    left: 0;
    right: 0;
    text-align: center;
    line-height: 1;
    white-space: nowrap;
  }
  .hosts {
    top: 99px;
    font-weight: 700;
    font-size: 159px;
    color: var(--orange);
    letter-spacing: -2px;
  }
  .tagline {
    top: 261px;
    font-weight: 300;
    font-size: 84px;
    color: var(--red);
    letter-spacing: 1px;
  }
  .show-title-top {
    top: 350px;
    font-weight: 700;
    font-size: 304px;
    color: var(--red);
    letter-spacing: -2px;
  }
  .show-title-bottom {
    top: 633px;
    font-weight: 700;
    font-size: 194px;
    color: var(--red);
    letter-spacing: -1px;
  }
  .daily-tips {
    top: 1087px;
    left: 212px;
    right: auto;
    display: flex;
    align-items: center;
    gap: 32px;
    font-weight: 300;
    font-size: 82px;
    color: var(--orange);
  }
  .daily-tips svg { width: 76px; height: 58px; }
</style>
</head>
<body>
<div class="cover">
  <svg class="bubbles" viewBox="0 0 1200 1200" width="1200" height="1200" aria-hidden="true">
    <path fill="var(--orange)" d="M640 880 C700 990 880 1010 925 1005 C910 1035 895 1050 895 1055 C893 1062 898 1063 905 1061 C960 1050 1010 1020 1010 997 C1130 972 1165 910 1165 875 C1165 840 1145 815 1125 800 Z"/>
    <path fill="var(--bubble-light)" d="M-10 130 C140 40 380 0 600 0 C820 0 1060 40 1210 150 L1210 750 C1060 850 860 910 690 916 C640 920 590 921 557 920 C600 1000 650 1050 662 1063 C672 1075 666 1085 640 1080 C500 1060 350 1020 272 882 C150 850 60 815 -10 760 Z"/>
  </svg>

  <div class="text-block hosts">Rob &amp; Kolette</div>
  <div class="text-block tagline">Talk With Founders About</div>
  <div class="text-block show-title-top">HARD</div>
  <div class="text-block show-title-bottom">CHOICES</div>

  <div class="text-block daily-tips">
    <svg viewBox="0 0 78 60" aria-hidden="true">
      <path fill="var(--orange)" d="M2 22 L20 38 L74 2 L76 5 L24 58 L20 58 Z"/>
    </svg>
    <span>Includes daily tips</span>
  </div>
</div>
</body>
</html>
```